German Headhunter/ HR Consultancy needs Business Cards Design

We need a business Card Design for our Company in Stuttgart. We are specialized as Headhunter/ HR Consultancy in Placement of specialist and managers in permanent employment. Please refer to our business logo.

```html
<!DOCTYPE html>
<html lang="de">
<head>
<meta charset="utf-8">
<title>Kernwerk Personalberatung – Visitenkarte</title>
<link rel="stylesheet" href="https://fonts.googleapis.com/css2?family=Arimo:wght@400;700&display=swap">
<style>
  :root {
    --brand-blue: #3a56a8;
    --paper: #ffffff;
    --ink: #1d1d22;
    --muted-grey: #8a8c92;
    --backdrop: #1f2024;
  }
  * { margin: 0; padding: 0; box-sizing: border-box; }
  html, body {
    width: 1200px; height: 948px; overflow: hidden;
    background: var(--backdrop);
    font-family: "Arimo", Arial, sans-serif;
  }
  .canvas { position: relative; width: 1200px; height: 948px; }

  .card {
    position: absolute; left: 250px;
    width: 700px; height: 400px;
    border-radius: 28px; overflow: hidden;
  }

  /* Front side */
  .card-front { top: 44px; background: var(--brand-blue); }
  .front-brand {
    position: absolute; left: 0; right: 0; top: 50%;
    transform: translateY(-50%);
    display: flex; align-items: center; justify-content: center; gap: 22px;
    color: var(--paper); font-weight: 700;
  }
  .front-brand .brand-square { width: 34px; height: 34px; background: var(--paper); }
  .front-brand .brand-name { display: flex; flex-direction: column; line-height: 1; }
  .front-brand .brand-name .word { font-size: 54px; letter-spacing: 2px; }
  .front-brand .brand-name .sub { font-size: 20px; letter-spacing: 3px; margin-top: 8px; }

  /* Back side */
  .card-back { top: 504px; background: var(--paper); }
  .back-brand {
    position: absolute; left: 70px; top: 52px;
    color: var(--brand-blue); font-weight: 700; line-height: 1;
  }
  .back-brand .word { font-size: 44px; letter-spacing: 2px; display: block; }
  .back-brand .sub { font-size: 17px; letter-spacing: 2.5px; display: block; margin-top: 6px; }

  .accent-bar {
    position: absolute; left: 0; top: 168px;
    width: 16px; height: 58px; background: var(--brand-blue);
  }
  .person { position: absolute; left: 70px; top: 166px; }
  .person-name {
    color: var(--brand-blue); font-weight: 700; font-size: 30px; letter-spacing: 1px;
  }
  .person-role { color: var(--ink); font-size: 17px; margin-top: 4px; }

  .address {
    position: absolute; left: 70px; top: 250px;
    color: var(--ink); font-size: 16px; line-height: 1.35; font-style: normal;
  }
  .contact-list {
    position: absolute; left: 70px; top: 302px; list-style: none;
    color: var(--ink); font-size: 16px;
  }
  .contact-list li { display: flex; align-items: center; gap: 10px; height: 24px; }
  .contact-list svg { width: 14px; height: 14px; fill: var(--brand-blue); flex: none; }
</style>
</head>
<body>
<main class="canvas">

  <section class="card card-front" aria-label="Vorderseite">
    <div class="front-brand">
      <span class="brand-square"></span>
      <span class="brand-name">
        <span class="word">KERNWERK</span>
        <span class="sub">PERSONALBERATUNG</span>
      </span>
    </div>
  </section>

  <section class="card card-back" aria-label="Rückseite">
    <div class="back-brand">
      <span class="word">KERNWERK</span>
      <span class="sub">PERSONALBERATUNG</span>
    </div>

    <span class="accent-bar"></span>
    <div class="person">
      <p class="person-name">JONAS WEBER</p>
      <p class="person-role">CEO/Founder</p>
    </div>

    <address class="address">
      2215 Lindenhof Straße<br>
      Suite B Stuttgart, 70173
    </address>

    <ul class="contact-list">
      <li>
        <svg viewBox="0 0 16 16" aria-hidden="true"><path d="M3.6 1.5l2.3 2.6-1.2 1.8c.9 2 2.4 3.5 4.4 4.4l1.8-1.2 2.6 2.3-1.3 2.1C7 13.4 2.6 9 2.5 2.8z"/></svg>
        (555) 010 - 2286
      </li>
      <li>
        <svg viewBox="0 0 16 16" aria-hidden="true"><path d="M1 3h14v10H1z M2 4.2v.3l6 4.3 6-4.3v-.3z" fill-rule="evenodd"/></svg>
        info@kernwerk-personal.com
      </li>
      <li>
        <svg viewBox="0 0 16 16" aria-hidden="true"><circle cx="8" cy="8" r="7"/><path d="M1 8h14M8 1c3 3.5 3 10.5 0 14M8 1c-3 3.5-3 10.5 0 14" stroke="#fff" stroke-width="1" fill="none"/></svg>
        www.kernwerk-personal.com
      </li>
    </ul>
  </section>

</main>
</body>
</html>
```